Business Cards Needed for Innovative Healthcare Marketing Company

We are a marketing company focused on healthcare. Our company is all about rebranding yourself renewing your image and generating results. The phoenix stands for "reborn" or "rising" which we provide new brands for our clients we take their old brands and renew it with creativity and innovation. I am looking for a business card with color dimension. I have attached an example of a card I think has the look and feel of what I am trying to accomplish. I like that the card example has black and grey font colors, I like the font placement and the small logo, I really like the use of the colors on the right those are the colors of my logo. My logo is phoenix so maybe incorporating flames similar to that design. I would like the back a solid color maybe red with an opaque version of the logo and website. As a marketing company I am always open to creative liberty!

Target Market(s)

Doctors and business professionals.

Industry/Entity Type

Marketing

Contact Information for Business Card

Valcorne Health Care Marketing
Marla Tenwick- CEO
#(512)638-2974
email-marla@valcorne.com
website- valcorne.com

Font styles to use
Sans Serif

Colors
ec1f27
f37122
ffc214
fbed22
fbf289
f04a50

Requirements
Must have
• The logo and required information
Nice to have
• icons by the information
Should not have
• child like font

```html
<!DOCTYPE html>
<html lang="en">
<head>
<meta charset="utf-8">
<title>Valcorne Health Care Marketing – Business Card</title>
<link rel="stylesheet" href="https://fonts.googleapis.com/css2?family=Open+Sans:wght@300;400;600;700&display=swap">
<style>
  :root {
    --stage: #ece7e4;
    --card-white: #ffffff;
    --brand-red: #a31d24;
    --brand-deep: #8f1a20;
    --name-red: #b5322a;
    --flame-yellow: #ffc214;
    --flame-orange: #f37122;
    --title-orange: #f7a21b;
    --text-grey: #4a4a4a;
    --back-text: rgba(255, 255, 255, 0.9);
  }
  * { box-sizing: border-box; margin: 0; padding: 0; }
  html, body {
    width: 1200px; height: 950px; overflow: hidden;
    background: var(--stage);
    font-family: "Open Sans", Arial, sans-serif;
  }
  .canvas { position: relative; width: 1200px; height: 950px; }

  .card {
    position: absolute; left: 230px; width: 740px; height: 422px;
    box-shadow: 0 10px 28px rgba(0, 0, 0, 0.18);
    overflow: hidden;
  }
  .card--front { top: 40px; background: var(--card-white); }
  .card--back { top: 492px; background: var(--brand-red); }

  .flame-art { position: absolute; top: 0; right: 0; width: 500px; height: 300px; }

  .brand { position: absolute; left: 48px; top: 168px; display: flex; align-items: center; gap: 14px; }
  .brand__dot { width: 38px; height: 38px; border-radius: 50%; background: var(--name-red); }
  .brand__name {
    font-weight: 300; font-size: 34px; letter-spacing: 3px; color: var(--name-red); line-height: 1;
  }
  .brand__tagline {
    display: block; font-size: 10.5px; font-weight: 400; letter-spacing: 2.4px;
    color: var(--title-orange); margin-top: 5px;
  }

  .person { position: absolute; left: 50px; top: 252px; }
  .person__name { font-weight: 700; font-size: 34px; color: var(--name-red); line-height: 1.1; }
  .person__title { font-weight: 400; font-size: 19px; color: var(--title-orange); margin-top: 2px; }

  .contact { position: absolute; left: 50px; top: 334px; list-style: none; }
  .contact__item {
    display: flex; align-items: center; gap: 10px;
    font-size: 14px; color: var(--text-grey); line-height: 1; margin-bottom: 7px;
  }
  .contact__icon {
    width: 15px; height: 15px; background: var(--name-red); color: #fff;
    font-size: 9px; font-weight: 600; display: flex; align-items: center; justify-content: center;
  }

  .back-mark {
    position: absolute; left: 50%; top: 50%; transform: translate(-50%, -50%);
    display: flex; align-items: center; gap: 14px;
  }
  .back-mark__dot { width: 40px; height: 40px; border-radius: 50%; background: rgba(255,255,255,0.85); }
  .back-mark__name { font-weight: 300; font-size: 38px; letter-spacing: 4px; color: var(--back-text); }

  .back-web {
    position: absolute; left: 46px; top: 50%;
    transform: translate(-50%, -50%) rotate(-90deg);
    font-size: 14px; letter-spacing: 5px; color: var(--back-text); white-space: nowrap;
  }
</style>
</head>
<body>
<main class="canvas">

  <section class="card card--front" aria-label="Business card front">
    <svg class="flame-art" viewBox="0 0 500 300" role="img" aria-label="Orange and yellow phoenix flame illustration">
      <defs>
        <linearGradient id="flameGradient" x1="0" y1="0" x2="1" y2="0.6">
          <stop offset="0" stop-color="var(--flame-yellow)"/>
          <stop offset="1" stop-color="var(--flame-orange)"/>
        </linearGradient>
      </defs>
      <path d="M40 0 H500 V300 C430 250 380 190 300 170 C220 150 150 120 110 80 C80 50 55 25 40 0 Z" fill="url(#flameGradient)"/>
    </svg>

    <div class="brand">
      <span class="brand__dot" aria-hidden="true"></span>
      <div>
        <span class="brand__name">VALCORNE</span>
        <span class="brand__tagline">HEALTHCARE MARKETING</span>
      </div>
    </div>

    <div class="person">
      <h1 class="person__name">Marla Tenwick</h1>
      <p class="person__title">CEO</p>
    </div>

    <ul class="contact">
      <li class="contact__item"><span class="contact__icon">p</span>(512)638-2974</li>
      <li class="contact__item"><span class="contact__icon">e</span>marla@valcorne.com</li>
      <li class="contact__item"><span class="contact__icon">w</span>www.valcorne.com</li>
    </ul>
  </section>

  <section class="card card--back" aria-label="Business card back">
    <div class="back-mark">
      <span class="back-mark__dot" aria-hidden="true"></span>
      <span class="back-mark__name">VALCORNE</span>
    </div>
    <p class="back-web">valcorne.com</p>
  </section>

</main>
</body>
</html>
```